R7M Horizon Business Card Design

We need a business card created for our New Business "R7M Horizon"<br/><br/>The business card design is up to you however the following information must be on the business card:<br/><br/>Front of the business card -<br/>Email :darrenp@r7mhorizon.nz<br/>Mobile: +64 (0) 22 4870 619<br/>Website: www.r7mhorizon.nz<br/>Card Owner Name: Darren Paltrow<br/>Company Title: Business Development Manager<br/>Slogan: "The BEST of both worlds". <br/>Logo On the front attached to the design brief<br/><br/>On the back: <br/>Space on the back for 4 more versions of the logo across the bottom of the card indicating different subsidiary brands - R7M Coffee, R7M Arts, R7M ?? (The card will be used for all of these brands - We Will add the extra subsidiary logos to the design once the design is finished (We are a graphics design team). <br/><br/>Other than that we want a premium feeling logo that remains universally usable depending on the business entity that we are using the card for. The use of bright bold colours would be great but we still want the card to feel premium.
Target Market(s)
Gift Design and Manufacturing Companies
Contact Information for Business Card
Front of the business card -
Email :darrenp@r7mhorizon.nz
Mobile: +64 (0) 22 4870 619
Website: www.r7mhorizon.nz
Card Owner Name: Darren Paltrow
Company Title: Business Development Manager
Slogan: "The BEST of both worlds".
Logo On the front attached to the design brief

```html
<!DOCTYPE html>
<html lang="en">
<head>
<meta charset="UTF-8">
<title>R7M Horizon Business Card</title>
<link href="https://fonts.googleapis.com/css2?family=Open+Sans:ital,wght@0,400;0,600;0,700;1,400;1,800&display=swap" rel="stylesheet">
<style>
  :root {
    --backdrop: #2b2b2d;
    --card: #1e1e20;
    --accent: #3646b4;
    --text-light: #f2f2f2;
    --emboss: #141416;
    --emboss-edge: #3a3a3e;
  }
  * { margin: 0; padding: 0; box-sizing: border-box; }
  html, body {
    width: 1200px; height: 900px; overflow: hidden;
    background: var(--backdrop);
    font-family: "Open Sans", Arial, sans-serif;
  }
  .canvas {
    width: 1200px; height: 900px;
    display: flex; flex-direction: column;
    align-items: center; justify-content: center; gap: 60px;
  }
  .card {
    position: relative;
    width: 630px; height: 360px;
    background: var(--card);
    border-bottom: 8px solid var(--accent);
    box-shadow: 0 10px 30px rgba(0,0,0,.45);
    color: var(--text-light);
  }
  .brand-dot { flex: none; border-radius: 50%; }
  .brand-name { font-weight: 700; white-space: nowrap; letter-spacing: .5px; }

  /* Front */
  .brand {
    position: absolute; left: 36px; top: 112px;
    display: flex; align-items: center; gap: 12px;
  }
  .brand .brand-dot { width: 30px; height: 30px; background: var(--accent); }
  .brand .brand-name { font-size: 28px; color: var(--accent); }
  .divider {
    position: absolute; left: 302px; top: 70px;
    width: 1px; height: 190px; background: var(--accent);
  }
  .details { position: absolute; left: 324px; top: 84px; }
  .person-name {
    font-weight: 800; font-style: italic; font-size: 20px;
    letter-spacing: 5px; text-transform: uppercase; color: var(--accent);
    white-space: nowrap;
  }
  .person-role { font-size: 16px; margin: 4px 0 18px; white-space: nowrap; }
  .contact-list { list-style: none; font-size: 16px; line-height: 1.7; }
  .contact-list li { display: flex; align-items: center; gap: 10px; white-space: nowrap; }
  .contact-list svg { width: 14px; height: 14px; fill: var(--text-light); flex: none; }
  .contact-list .web-host { color: var(--accent); }
  .slogan { position: absolute; font-size: 19px; color: var(--text-light); white-space: nowrap; }
  .slogan strong { font-weight: 400; color: var(--accent); }
  .card-front .slogan { left: 36px; bottom: 34px; }

  /* Back */
  .brand-lines {
    position: absolute; right: 36px; top: 26px;
    font-size: 18px; color: var(--accent); letter-spacing: .5px;
  }
  .brand-emboss {
    position: absolute; left: 50%; top: 140px; transform: translateX(-50%);
    display: flex; align-items: center; gap: 16px;
  }
  .brand-emboss .brand-name { color: var(--emboss); font-size: 46px; }
  .brand-emboss .brand-dot {
    width: 44px; height: 44px; background: var(--emboss);
    border: 1px solid var(--emboss-edge);
  }
  .card-back .slogan { left: 50%; transform: translateX(-50%); bottom: 40px; }
</style>
</head>
<body>
<main class="canvas">
  <section class="card card-front" aria-label="Card front">
    <div class="brand">
      <span class="brand-dot"></span>
      <span class="brand-name">R7M Horizon</span>
    </div>
    <div class="divider"></div>
    <div class="details">
      <h1 class="person-name">Darren Paltrow</h1>
      <p class="person-role">Business Development Manager</p>
      <ul class="contact-list">
        <li><svg viewBox="0 0 16 16" aria-hidden="true"><path d="M4 0h8a1 1 0 0 1 1 1v14a1 1 0 0 1-1 1H4a1 1 0 0 1-1-1V1a1 1 0 0 1 1-1zm1 2v10h6V2zm3 11a1 1 0 1 0 0 2 1 1 0 0 0 0-2z"/></svg><span>+64 (0) 22 4870 619</span></li>
        <li><svg viewBox="0 0 16 16" aria-hidden="true"><path d="M0 3h16v1L8 9 0 4zm0 3l8 5 8-5v7H0z"/></svg><span>darrenp@r7mhorizon.nz</span></li>
        <li><svg viewBox="0 0 16 16" aria-hidden="true"><path d="M8 0a8 8 0 1 0 0 16A8 8 0 0 0 8 0zm0 1.5c1 0 2 2 2.3 5H5.7C6 3.5 7 1.5 8 1.5zM5.7 8h4.6C10 11.5 9 14.5 8 14.5S6 11.5 5.7 8zM1.6 8h2.6c.1 2.4.6 4.5 1.4 5.7A6.5 6.5 0 0 1 1.6 8zm8.8 5.7c.8-1.2 1.3-3.3 1.4-5.7h2.6a6.5 6.5 0 0 1-4 5.7zm1.4-7.2c-.1-2.2-.6-4-1.4-5.2a6.5 6.5 0 0 1 4 5.2zm-7.6 0H1.6a6.5 6.5 0 0 1 4-5.2C4.8 2.5 4.3 4.3 4.2 6.5z"/></svg><span>www.<span class="web-host">r7mhorizon</span>.nz</span></li>
      </ul>
    </div>
    <p class="slogan">The <strong>BEST</strong> of both worlds</p>
  </section>

  <section class="card card-back" aria-label="Card back">
    <p class="brand-lines">GIFTS, ART, COFFEE, ????</p>
    <div class="brand-emboss">
      <span class="brand-name">R7M Horizon</span>
      <span class="brand-dot"></span>
    </div>
    <p class="slogan">The <strong>BEST</strong> of both worlds</p>
  </section>
</main>
</body>
</html>
```